Harborline Auto LLC

Car Dealer Customer Service
Address: 2874 Cresthaven Road, Shelbyville, TN 37162
web: www.harborlineautoxq.net
email: harborlineautoxq@mailnest.example
Phone: (931) 555-0148
Phone: (629) 555-0173

```html
<!DOCTYPE html>
<html lang="en">
<head>
<meta charset="utf-8">
<title>Harborline Auto – Business Card</title>
<link href="https://fonts.googleapis.com/css2?family=Montserrat:wght@500;800&display=swap" rel="stylesheet">
<style>
  :root{
    --stage:#2b2b2d;
    --brand-blue:#1b7aab;
    --accent-blue:#2a90c9;
    --accent-gold:#eab444;
    --card-white:#ffffff;
    --ink:#1c1c1c;
  }
  *{margin:0;padding:0;box-sizing:border-box}
  html,body{width:1200px;height:960px;overflow:hidden;background:var(--stage)}
  .stage{width:1200px;height:960px;display:flex;flex-direction:column;align-items:center;justify-content:center;gap:48px}
  .card{width:640px;height:366px;border-radius:22px;position:relative;overflow:hidden;box-shadow:0 14px 30px rgba(0,0,0,.45)}
  .card-front{background:var(--brand-blue);display:flex;align-items:center;justify-content:center;gap:18px}
  .brand-dot{width:34px;height:34px;border-radius:50%;background:var(--card-white)}
  .brand-name{font-family:"Montserrat",sans-serif;font-weight:800;font-size:44px;letter-spacing:1px;color:var(--card-white);text-transform:uppercase}
  .card-back{background:var(--card-white)}
  .back-brand{position:absolute;left:24px;top:120px;width:256px;text-align:center}
  .back-brand .brand-name{color:var(--accent-blue);font-size:30px;line-height:1.15}
  .divider{position:absolute;left:298px;top:52px;width:2px;height:190px;background:var(--accent-blue)}
  .contact{position:absolute;left:318px;top:58px;width:304px;font-family:"Montserrat",sans-serif;font-weight:500;color:var(--ink);font-size:14px;line-height:1.5}
  .contact .role{margin-bottom:2px}
  .contact .address{margin-bottom:6px}
  .contact .row{display:flex;align-items:center;gap:8px;font-size:13px;white-space:nowrap}
  .contact .row svg{width:14px;height:14px;flex:none}
  .web-host{color:var(--accent-blue)}
  .bands{position:absolute;left:0;bottom:0;width:640px;height:366px}
</style>
</head>
<body>
<main class="stage">
  <section class="card card-front" aria-label="Card front">
    <span class="brand-dot"></span>
    <span class="brand-name">Harborline Auto</span>
  </section>

  <section class="card card-back" aria-label="Card back">
    <svg class="bands" viewBox="0 0 640 366" aria-hidden="true">
      <path d="M0 344 L450 344 L466 290 L640 290 L640 366 L0 366 Z" fill="var(--accent-blue)"/>
      <path d="M0 324 L168 324 L168 334 L0 334 Z" fill="var(--accent-gold)"/>
      <path d="M174 324 L306 324 L306 334 L174 334 Z" fill="var(--accent-blue)"/>
      <path d="M312 324 L452 324 L446 334 L312 334 Z" fill="var(--accent-gold)"/>
    </svg>

    <div class="back-brand"><span class="brand-name">Harborline Auto</span></div>
    <div class="divider"></div>

    <div class="contact">
      <p class="role">Car Dealer Customer Service</p>
      <p class="address">2874 Cresthaven Road,<br>Shelbyville, TN 37162</p>
      <p class="row"><svg viewBox="0 0 14 14"><path d="M3 1 L5.5 3.5 L4 5.5 Q6 8.5 8.5 10 L10.5 8.5 L13 11 L11 13 Q5 12 1 3 Z" fill="var(--accent-blue)"/></svg><span>(931) 555-0148</span></p>
      <p class="row"><svg viewBox="0 0 14 14"><rect x="2" y="6" width="10" height="7" rx="1" fill="var(--accent-blue)"/><path d="M1 5 Q7 0 13 5 L11 6 Q7 3 3 6 Z" fill="var(--accent-blue)"/></svg><span>(629) 555-0173</span></p>
      <p class="row"><svg viewBox="0 0 14 14"><rect x="1" y="3" width="12" height="8" fill="var(--accent-blue)"/><path d="M1 3 L7 8 L13 3" stroke="#fff" stroke-width="1.2" fill="none"/></svg><span>harborlineautoxq@mailnest.example</span></p>
      <p class="row"><svg viewBox="0 0 14 14"><circle cx="7" cy="7" r="6" fill="var(--accent-blue)"/></svg><span>www.<span class="web-host">harborlineautoxq</span>.net</span></p>
    </div>
  </section>
</main>
</body>
</html>
```